Four in One (Flexible infographic for Content Management Industry)

See attachment.
A graphic depicting 4 products, where each can stand on its own and each can be combined with others, but where, if all are taken together, the best result is achieved (the "super product").
Intended use is web. See attached file as an example.
The most basic idea is as the attached diagram shows, where 4 rectangles are arranged in a quadrangle, with a middle rectangle in the center representing the combined 4 products. This concept is fine except it is a bit too obvious as it stands. We are looking for either a variation of this or another concept.
The audience is technical + professional + enterprise - NOT consumers. Hence the design should be conservative in nature.
We are aware of tools like as Canva or Pictogram where such graphics are available, but we are looking for something with a bit more imagination and flexibility.
This graphic should be targeted to web sites and be delivered with vector-based (SVG) graphics.

```html
<!DOCTYPE html>
<html lang="en">
<head>
<meta charset="utf-8">
<title>Four in One – Super Product</title>
<link href="https://fonts.googleapis.com/css2?family=Poppins:wght@400;500;600;700&family=Bebas+Neue&display=swap" rel="stylesheet">
<style>
:root{
  --ink:#151a33;
  --body:#23263a;
  --doc:#1e3a9e;
  --doc-line:#3cc4ea;
  --sec:#8b1cb0;
  --sec-line:#7a1fa6;
  --erp:#f0407a;
  --erp-line:#f0507a;
  --dig:#5b1fb8;
  --dig-line:#6a22b0;
  --page:#ffffff;
}
*{margin:0;padding:0;box-sizing:border-box}
html,body{width:1200px;height:867px;overflow:hidden;background:var(--page)}
.canvas{position:relative;width:1200px;height:867px;font-family:'Poppins',sans-serif;color:var(--body)}
.shapes{position:absolute;left:0;top:0}
.title{position:absolute;font-weight:700;font-size:20px;line-height:20px;color:var(--ink);letter-spacing:.2px}
.title span{display:block}
.desc{position:absolute;font-size:12.4px;line-height:14.8px;color:var(--body)}
.features{position:absolute;list-style:none}
.features li{position:relative;height:19px;font-size:12.4px;font-weight:600;line-height:19px;color:var(--ink);padding-left:19px}
.features li::before{content:"";position:absolute;left:0;top:5px;width:10px;height:10px;border-radius:50%;background:var(--tick)}
.features li::after{content:"";position:absolute;left:3.2px;top:7.4px;width:3.6px;height:2px;border-left:1.6px solid #fff;border-bottom:1.6px solid #fff;transform:rotate(-45deg)}
.doc{--tick:var(--doc)} .sec{--tick:var(--sec)} .erp{--tick:var(--erp)} .dig{--tick:var(--dig)}
.btn{position:absolute;width:136px;height:23px;border-radius:12px;color:#fff;font-size:16px;font-weight:500;line-height:23px;text-align:center}
.btn.doc-btn{background:linear-gradient(90deg,#2196f3,#3ad9e8);color:var(--ink)}
.btn.sec-btn{background:linear-gradient(90deg,#6a11cb,#d01fa5)}
.btn.erp-btn{background:linear-gradient(90deg,#ff4f7b,#ffe640);color:var(--ink)}
.btn.dig-btn{background:linear-gradient(90deg,#4a1aa8,#4a6ef0)}
.hub{position:absolute;left:494px;top:329px;width:200px;height:200px;display:flex;flex-direction:column;align-items:center;justify-content:center;font-family:'Bebas Neue',sans-serif;font-size:52px;line-height:44px;color:#0c0c14}
</style>
</head>
<body>
<div class="canvas">
<svg class="shapes" width="1200" height="867" viewBox="0 0 1200 867">
  <defs>
    <filter id="cardShadow" x="-10%" y="-10%" width="125%" height="130%">
      <feDropShadow dx="4" dy="8" stdDeviation="8" flood-color="#000" flood-opacity=".22"/>
    </filter>
    <linearGradient id="leafDoc" x1="0" y1="0" x2="1" y2="1"><stop offset="0" stop-color="#4ee3e3"/><stop offset="1" stop-color="#29b6f6"/></linearGradient>
    <linearGradient id="leafSec" x1="0" y1="0" x2="1" y2="1"><stop offset="0" stop-color="#d010a6"/><stop offset="1" stop-color="#7a12b0"/></linearGradient>
    <linearGradient id="leafErp" x1="1" y1="0" x2="0" y2="1"><stop offset="0" stop-color="#ffa45a"/><stop offset="1" stop-color="#ff3b82"/></linearGradient>
    <linearGradient id="leafDig" x1="0" y1="0" x2="1" y2="1"><stop offset="0" stop-color="#3e6ee8"/><stop offset="1" stop-color="#6a16b0"/></linearGradient>
    <radialGradient id="hubFill" cx=".5" cy=".55" r=".55"><stop offset=".35" stop-color="#00e8d8"/><stop offset=".7" stop-color="#0a9de0"/><stop offset="1" stop-color="#0c1790"/></radialGradient>
    <linearGradient id="arcDoc" x1="0" y1="0" x2="1" y2="1"><stop offset="0" stop-color="#3cc4ea"/><stop offset="1" stop-color="#7ef0d0"/></linearGradient>
    <linearGradient id="arcSec" x1="0" y1="0" x2="1" y2="1"><stop offset="0" stop-color="#e0409a"/><stop offset="1" stop-color="#8b1cb0"/></linearGradient>
    <linearGradient id="arcErp" x1="0" y1="0" x2="1" y2="1"><stop offset="0" stop-color="#ffe640"/><stop offset="1" stop-color="#f0407a"/></linearGradient>
    <linearGradient id="arcDig" x1="0" y1="0" x2="1" y2="1"><stop offset="0" stop-color="#4a6ef0"/><stop offset="1" stop-color="#6a22b0"/></linearGradient>
  </defs>

  <!-- cards -->
  <g filter="url(#cardShadow)" fill="#fff">
    <rect x="99" y="129" width="453" height="294" rx="26"/>
    <rect x="651" y="129" width="455" height="294" rx="26"/>
    <rect x="96" y="445" width="456" height="294" rx="26"/>
    <rect x="651" y="445" width="456" height="294" rx="26"/>
  </g>

  <!-- card frames -->
  <g fill="none" stroke-width="1.6">
    <rect x="120" y="154" width="413" height="242" rx="20" stroke="var(--doc-line)"/>
    <rect x="673" y="154" width="412" height="242" rx="20" stroke="var(--sec-line)"/>
    <rect x="119" y="469" width="410" height="245" rx="20" stroke="var(--erp-line)"/>
    <rect x="673" y="470" width="412" height="244" rx="20" stroke="var(--dig-line)"/>
  </g>

  <!-- corner leaves -->
  <path d="M98,207 V155 Q98,129 124,129 H173 Q173,207 98,207 Z" fill="url(#leafDoc)"/>
  <path d="M1107,207 V155 Q1107,129 1081,129 H1014 Q1014,207 1107,207 Z" fill="url(#leafSec)"/>
  <path d="M96,529 V471 Q96,445 122,445 H174 Q174,529 96,529 Z" fill="url(#leafErp)"/>
  <path d="M1107,527 V471 Q1107,445 1081,445 H1014 Q1014,527 1107,527 Z" fill="url(#leafDig)"/>

  <!-- orbit arcs -->
  <g fill="none" stroke-width="2">
    <path d="M585,316 V304 Q585,298 578,299 A132,132 0 0 0 462,412 Q461,424 470,424" stroke="url(#arcDoc)"/>
    <path d="M603,316 V304 Q603,298 610,299 A132,132 0 0 1 726,412 Q727,424 718,424" stroke="url(#arcSec)"/>
    <path d="M470,440 Q461,440 462,452 A132,132 0 0 0 578,563 Q585,564 585,558 V546" stroke="url(#arcErp)"/>
    <path d="M718,440 Q727,440 726,452 A132,132 0 0 1 610,563 Q603,564 603,558 V546" stroke="url(#arcDig)"/>
  </g>

  <!-- hub -->
  <circle cx="594" cy="429" r="111" fill="#fff" filter="url(#cardShadow)"/>
  <circle cx="594" cy="429" r="111" fill="none" stroke="#e4e6ea" stroke-width="3"/>
  <circle cx="594" cy="429" r="99" fill="url(#hubFill)"/>

  <!-- document icon -->
  <g transform="translate(178,166)">
    <path d="M0,4 Q0,0 4,0 H20 L30,10 V34 Q30,38 26,38 H4 Q0,38 0,34 Z" fill="#1e3a9e"/>
    <path d="M20,0 V10 H30" fill="#6a8be8"/>
    <g stroke="#fff" stroke-width="2.4" stroke-linecap="round"><line x1="6" y1="14" x2="20" y2="14"/><line x1="6" y1="20" x2="18" y2="20"/><line x1="6" y1="26" x2="14" y2="26"/></g>
    <circle cx="29" cy="30" r="8" fill="#29b6f6" stroke="#fff" stroke-width="1.5"/>
    <circle cx="29" cy="30" r="3" fill="#fff"/>
  </g>

  <!-- shield icon -->
  <g transform="translate(713,171)">
    <circle cx="22" cy="23" r="21" fill="none" stroke="var(--sec)" stroke-width="2"/>
    <path d="M22,8 L35,13 V23 Q35,33 22,39 Q9,33 9,23 V13 Z" fill="var(--sec)"/>
    <rect x="17" y="21" width="10" height="8" rx="1.5" fill="#fff"/>
    <path d="M19,21 V18 Q19,15 22,15 Q25,15 25,18 V21" fill="none" stroke="#fff" stroke-width="1.8"/>
    <circle cx="4" cy="37" r="3" fill="#e0409a"/><circle cx="38" cy="6" r="3" fill="#e0409a"/>
  </g>

  <!-- erp chip icon -->
  <g transform="translate(178,492)" fill="#ffa45a">
    <rect x="11" y="11" width="24" height="24" rx="3" fill="none" stroke="#ffa45a" stroke-width="2"/>
    <circle cx="23" cy="23" r="8" fill="var(--erp)"/><circle cx="23" cy="23" r="3.5" fill="#fff"/>
    <circle cx="15" cy="3" r="3"/><circle cx="23" cy="3" r="3"/><circle cx="31" cy="3" r="3"/>
    <circle cx="15" cy="43" r="3"/><circle cx="23" cy="43" r="3"/><circle cx="31" cy="43" r="3"/>
    <circle cx="3" cy="15" r="3"/><circle cx="3" cy="23" r="3"/><circle cx="3" cy="31" r="3"/>
    <circle cx="43" cy="15" r="3"/><circle cx="43" cy="23" r="3"/><circle cx="43" cy="31" r="3"/>
  </g>

  <!-- gear icon -->
  <g transform="translate(730,498)">
    <path d="M22,2 A20,20 0 1 0 22,40 V32 A11,11 0 1 1 22,10 Z" fill="#1e3a9e"/>
    <g fill="#1e3a9e"><rect x="7" y="0" width="6" height="6"/><rect x="0" y="18" width="6" height="6"/><rect x="7" y="36" width="6" height="6"/></g>
    <circle cx="22" cy="21" r="5" fill="#8b1cb0"/>
    <g stroke="#8b1cb0" stroke-width="2" fill="none"><path d="M25,8 H33"/><path d="M27,15 H40"/><path d="M27,21 H36"/><path d="M27,27 H40"/><path d="M25,34 H33"/></g>
    <g fill="#8b1cb0"><circle cx="35" cy="8" r="2.5"/><circle cx="41" cy="15" r="2.5"/><circle cx="38" cy="21" r="2.5"/><circle cx="41" cy="27" r="2.5"/><circle cx="35" cy="34" r="2.5"/></g>
  </g>
</svg>

<!-- Document Management -->
<h2 class="title" style="left:232px;top:168px"><span>DOCUMENT</span><span style="color:var(--doc)">MANAGEMENT</span></h2>
<p class="desc" style="left:130px;top:229px;width:400px">Streamline document organization, access, and collaboration with easier file storage and sharing, leading to more efficient workflows.</p>
<ul class="features doc" style="left:130px;top:284px">
  <li>Centralized Document Control</li>
  <li>Collaborative Workspace Integration</li>
  <li>Automated Compliance Tracking</li>
  <li>Check 4</li>
</ul>
<div class="btn doc-btn" style="left:246px;top:373px">Learn more</div>

<!-- Security & Compliance -->
<h2 class="title" style="left:780px;top:177px"><span>SECURITY &amp;</span><span style="color:var(--sec)">COMPLIANCE</span></h2>
<p class="desc" style="left:713px;top:229px;width:340px">Benefit from tailored cloud solutions, secure data storage, and expert disaster recovery planning for reliable and scalable IT operations.</p>
<ul class="features sec" style="left:717px;top:283px">
  <li>Custom Cloud Solutions</li>
  <li>Secure Data Storage</li>
  <li>Expert Disaster Recovery</li>
  <li>Check 4</li>
</ul>
<div class="btn sec-btn" style="left:809px;top:373px">Learn more</div>

<!-- Enterprise Resource Planning -->
<h2 class="title" style="left:242px;top:497px"><span>ENTERPRISE</span><span style="color:var(--erp);margin-top:2px">RESOURCE PLANNING</span></h2>
<p class="desc" style="left:130px;top:560px;width:400px">Simplify management across finance, sales, and operations, enabling better decision-making and improved productivity.</p>
<ul class="features erp" style="left:131px;top:598px">
  <li style="padding-left:21px">Integrated Business Processes</li>
  <li style="padding-left:21px">Enhanced Decision-Making</li>
  <li style="padding-left:21px">Productivity Improvement</li>
  <li style="padding-left:21px">Check 4</li>
</ul>
<div class="btn erp-btn" style="left:249px;top:690px">Learn more</div>

<!-- Digital Transformation -->
<h2 class="title" style="left:789px;top:502px"><span>DIGITAL</span><span style="color:var(--dig)">TRANSFORMATION</span></h2>
<p class="desc" style="left:697px;top:559px;width:350px">Turn scanned documents into easily searchable digital archives, boosting efficiency and accessibility.</p>
<ul class="features dig" style="left:698px;top:597px">
  <li style="padding-left:22px">Instant searchable Archives with OCR</li>
  <li style="padding-left:22px">Automated Document Classification</li>
  <li style="padding-left:22px">TeamPortal and Cloud Blob Ready</li>
  <li style="padding-left:22px">Check 4</li>
</ul>
<div class="btn dig-btn" style="left:809px;top:690px">Learn more</div>

<!-- Hub -->
<div class="hub"><span>SUPER</span><span>PRODUCT</span></div>
</div>
</body>
</html>
```